business card - Helicopter Flight Services, Flight School, etc.

We need a business card design for a new helicopter service.

We offer Helicopter Flight Services, Aerial Filming & Photography, Flight School, and Helicopter Tours. In that order.

Summit BladeAir, Inc.
Dennis Tollerby
SummitBladeair@Kestmail.com
626-418-7352

Based at the Brenwick Airport in Van Nuys, CA. The final design should communicate integrity and safety. Pictures or logos at your discretion.

Card back side - surprise me.

```html
<!DOCTYPE html>
<html lang="en">
<head>
<meta charset="utf-8">
<title>Summit BladeAir, Inc. — Business Card</title>
<link rel="stylesheet" href="https://fonts.googleapis.com/css2?family=Bodoni+Moda:wght@500;600&family=Arimo:wght@400&display=swap">
<style>
  :root {
    --backdrop: #d9d4cc;
    --navy: #0b0f4a;
    --navy-wave: #1a1c55;
    --ink: #050507;
    --silver: #e6e8ef;
    --title-ink: #101014;
    --rule: #c9cbd3;
    --sunset-top: #3a3570;
    --sunset-mid: #b48ab0;
    --sunset-low: #d8c4cf;
    --sea-deep: #112a45;
    --sea-light: #2e4a6c;
  }
  * { margin: 0; padding: 0; box-sizing: border-box; }
  html, body { width: 1200px; height: 902px; overflow: hidden; }
  body {
    background: var(--backdrop);
    display: flex;
    align-items: center;
    justify-content: center;
    gap: 30px;
  }
  .card {
    position: relative;
    width: 560px;
    height: 320px;
    overflow: hidden;
    box-shadow: 0 6px 18px rgba(0,0,0,.28);
  }

  /* Back side */
  .card-back {
    background: var(--navy);
    display: flex;
    flex-direction: column;
    align-items: center;
    justify-content: center;
    color: var(--silver);
    font-family: "Bodoni Moda", serif;
  }
  .card-back .company {
    font-size: 36px;
    font-weight: 600;
    letter-spacing: 2px;
    text-transform: uppercase;
  }
  .card-back .services {
    margin-top: 6px;
    font-size: 22px;
    font-weight: 500;
    letter-spacing: 1px;
  }

  /* Front side */
  .card-front { background: var(--ink); }
  .card-front .artwork { position: absolute; inset: 0; }
  .card-front .title-band {
    position: absolute;
    left: 0; right: 0; top: 62px;
    height: 60px;
    background: rgba(255,255,255,.38);
  }
  .card-front .company {
    position: absolute;
    left: 0; right: 0; top: 68px;
    text-align: center;
    font-family: "Bodoni Moda", serif;
    font-size: 38px;
    font-weight: 600;
    letter-spacing: 2px;
    text-transform: uppercase;
    color: var(--title-ink);
  }
  .card-front .holder {
    position: absolute;
    left: 36px; top: 250px;
    font-family: "Bodoni Moda", serif;
    font-size: 27px;
    font-weight: 600;
    color: var(--silver);
  }
  .card-front .divider {
    position: absolute;
    left: 292px; top: 176px;
    width: 1px; height: 118px;
    background: var(--rule);
  }
  .contact-list {
    position: absolute;
    left: 310px; top: 172px;
    list-style: none;
    font-family: "Arimo", sans-serif;
    font-size: 14.5px;
    color: var(--silver);
    line-height: 1.3;
  }
  .contact-list li {
    display: flex;
    align-items: flex-start;
    gap: 8px;
    margin-bottom: 9px;
  }
  .contact-list svg { flex: none; margin-top: 2px; }
</style>
</head>
<body>

  <section class="card card-back" aria-label="Card back">
    <h1 class="company">Summit BladeAir, Inc.</h1>
    <p class="services">Airport · Tour guide · Heliport</p>
  </section>

  <section class="card card-front" aria-label="Card front">
    <svg class="artwork" width="560" height="320" viewBox="0 0 560 320">
      <defs>
        <linearGradient id="sunset" x1="0" y1="0" x2="0" y2="1">
          <stop offset="0" stop-color="var(--sunset-top)"/>
          <stop offset=".45" stop-color="var(--sunset-mid)"/>
          <stop offset=".75" stop-color="var(--sunset-low)"/>
          <stop offset="1" stop-color="var(--sea-light)"/>
        </linearGradient>
        <linearGradient id="sea" x1="0" y1="0" x2="1" y2="1">
          <stop offset="0" stop-color="var(--sea-light)"/>
          <stop offset="1" stop-color="var(--sea-deep)"/>
        </linearGradient>
      </defs>
      <rect x="0" y="0" width="290" height="260" fill="url(#sunset)"
            role="img" aria-label="Photo of a helicopter on a pad at sunset over water"/>
      <rect x="290" y="0" width="270" height="200" fill="url(#sea)"
            role="img" aria-label="Photo of a speedboat racing across open water"/>
      <path d="M0 200 C120 260 300 250 400 180 C460 140 510 135 560 140 L560 320 L0 320 Z"
            fill="var(--navy-wave)" opacity=".85"/>
      <path d="M0 240 C130 290 320 270 420 205 C480 170 520 165 560 168 L560 320 L0 320 Z"
            fill="var(--ink)"/>
    </svg>

    <div class="title-band"></div>
    <h1 class="company">Summit BladeAir, Inc.</h1>

    <p class="holder">Dennis Tollerby</p>
    <div class="divider"></div>

    <ul class="contact-list">
      <li>
        <svg width="12" height="12" viewBox="0 0 12 12"><rect width="12" height="12" rx="2" fill="var(--silver)"/><path d="M3.5 2.5 L5 4 L4.2 5 Q5.5 7 7 7.8 L8 7 L9.5 8.5 L8.6 9.5 Q5 9 2.6 3.4 Z" fill="var(--ink)"/></svg>
        <span>626-418-7352</span>
      </li>
      <li>
        <svg width="12" height="12" viewBox="0 0 12 12"><rect width="12" height="12" rx="2" fill="var(--silver)"/><rect x="2.5" y="3.5" width="7" height="5" fill="none" stroke="var(--ink)" stroke-width="1"/><path d="M2.5 3.5 L6 6.5 L9.5 3.5" fill="none" stroke="var(--ink)" stroke-width="1"/></svg>
        <span>SummitBladeair@Kestmail.com</span>
      </li>
      <li>
        <svg width="12" height="12" viewBox="0 0 12 12"><rect width="12" height="12" rx="2" fill="var(--silver)"/><path d="M6 10 L3.6 6 A2.8 2.8 0 1 1 8.4 6 Z" fill="var(--ink)"/><circle cx="6" cy="4.6" r="1" fill="var(--silver)"/></svg>
        <span>2740 W. Larkspur Ave. Ste.B<br>Corvan, CA 91520</span>
      </li>
    </ul>
  </section>

</body>
</html>
```